Australian Trucking Company Requires Professional Looking Stationary

We require a professional looking stationary design that incorporates our newly designed logo.

Our business, called "Brell Haulage Contracting", provides contracting work, transport and logistics to business in Western Australia particularly with links to the mining sector.

We are a small business looking to expand and our new logo and our new stationary will help develop our brand image in our market place.

Target Market(s)

Businesses and Corporation with links to the Mining Sector

Industry/Entity Type

Small Business

Requirements
Must have
• The letterhead must have the following details:
The new logo

Text saying: "Brell Holdings Pty Ltd (ACN 582 316 907) ATF The Brell Discretionary Trust T/AS"
"ABN 71 834 209 553"
Address "P.O Box 817 Wattlegrove WA, 6958"
Phone: 08 9352 7140
Email: brellhaul@mailbox-example.com.au

The text on the letterhead should be editable as the details are likely to change in the near future. Provision should be made for a website address all though one isn't available at the moment.

The styling, layout and font text is entirely up to the designer.

```html
<!DOCTYPE html>
<html lang="en">
<head>
<meta charset="utf-8">
<title>Brell Haulage Contracting – Business Card</title>
<link rel="stylesheet" href="https://fonts.googleapis.com/css2?family=Exo+2:wght@400&display=swap">
<style>
  :root {
    --page-bg: #e4e7e9;
    --card-grey: #5a5a5b;
    --card-white: #ffffff;
    --brand-red: #d3262b;
    --band-red: #bf2026;
    --ink: #2b2b2b;
    --icon-grey: #4a4a4a;
    --mark-light: #ffffff;
    --mark-grey: #8a8a8a;
  }
  * { box-sizing: border-box; margin: 0; padding: 0; }
  html, body { width: 1200px; height: 960px; overflow: hidden; }
  body {
    background: var(--page-bg);
    font-family: "Exo 2", sans-serif;
    font-weight: 400;
    display: flex;
    flex-direction: column;
    align-items: center;
    justify-content: center;
    gap: 36px;
  }
  .card {
    position: relative;
    width: 700px;
    height: 428px;
    overflow: hidden;
    box-shadow: 0 6px 18px rgba(0,0,0,0.18);
  }
  .card--front { background: var(--card-grey); }
  .card--back { background: var(--card-white); }

  .rule {
    position: absolute;
    height: 3px;
    background: var(--brand-red);
  }
  .rule--top { top: 92px; left: 330px; right: 0; }
  .rule--bottom { bottom: 92px; left: 0; width: 370px; }

  .company {
    position: absolute;
    display: flex;
    align-items: center;
  }
  .company__mark { flex: none; }
  .company__name {
    font-weight: 400;
    letter-spacing: 0.03em;
    white-space: nowrap;
  }

  .card--front .company {
    left: 170px;
    top: 182px;
    gap: 18px;
  }
  .card--front .company__mark { width: 62px; height: 62px; background: var(--mark-light); }
  .card--front .company__name { font-size: 28px; color: var(--mark-light); }

  .card--back .company {
    right: 44px;
    bottom: 76px;
    gap: 12px;
  }
  .card--back .company__mark { width: 40px; height: 40px; background: var(--mark-grey); }
  .card--back .company__name { font-size: 19px; color: var(--ink); }

  .name-band {
    position: absolute;
    top: 52px;
    left: 0;
    width: 330px;
    height: 64px;
    background: var(--band-red);
    color: #ffffff;
    padding: 8px 0 0 64px;
  }
  .name-band__name { font-size: 24px; letter-spacing: 0.04em; line-height: 1.1; }
  .name-band__title { font-size: 17px; letter-spacing: 0.04em; line-height: 1.2; }

  .contact {
    position: absolute;
    left: 64px;
    top: 148px;
    list-style: none;
    color: var(--ink);
    font-size: 19px;
    letter-spacing: 0.04em;
  }
  .contact__item {
    display: flex;
    align-items: flex-start;
    gap: 14px;
    line-height: 1.2;
  }
  .contact__item--address { margin-top: 18px; }
  .contact__icon { width: 14px; height: 14px; margin-top: 4px; flex: none; fill: var(--icon-grey); }
</style>
</head>
<body>

  <section class="card card--front" aria-label="Card front">
    <div class="rule rule--top"></div>
    <div class="company">
      <span class="company__mark"></span>
      <span class="company__name">Brell Haulage Contracting</span>
    </div>
    <div class="rule rule--bottom"></div>
  </section>

  <section class="card card--back" aria-label="Card back">
    <div class="name-band">
      <p class="name-band__name">Tobias Renwick</p>
      <p class="name-band__title">President</p>
    </div>
    <ul class="contact">
      <li class="contact__item">
        <svg class="contact__icon" viewBox="0 0 16 16" aria-hidden="true"><path d="M3.6 1.2l2.2 2.6-1.3 1.8c.9 2 2.4 3.5 4.4 4.4l1.8-1.3 2.6 2.2-1.4 2.3C6.8 14.8 1.2 9.2 1.3 2.6z"/></svg>
        <span>08 9352 7140</span>
      </li>
      <li class="contact__item">
        <svg class="contact__icon" viewBox="0 0 16 16" aria-hidden="true"><path d="M1 3h14v10H1z M1.5 3.5L8 9l6.5-5.5" stroke="#fff" stroke-width="1.2"/></svg>
        <span>brellhaul@mailbox-example.com.au</span>
      </li>
      <li class="contact__item contact__item--address">
        <svg class="contact__icon" viewBox="0 0 16 16" aria-hidden="true"><circle cx="8" cy="8" r="7"/><path d="M1 8h14M8 1c-3 3-3 11 0 14M8 1c3 3 3 11 0 14" stroke="#fff" stroke-width="1" fill="none"/></svg>
        <span>P.O Box 817<br>Wattlegrove WA, 6958</span>
      </li>
    </ul>
    <div class="company">
      <span class="company__mark"></span>
      <span class="company__name">Brell Haulage Contracting</span>
    </div>
  </section>

</body>
</html>
```